Protective Security Officer services company needs logo and e mail stationary design

We need a logo design that compliments our vehicle wraps. We provide armed guards to the federal government. We want to use patriotic flag colors of red, white and blue. We like the name ORVA with the red swish. See vehicle pictures.
We provide armed guards to various departments of the federal government including : Civic Shield Bureau, National Guardpost Agency, All of the armed forces Navy , Air Force, Army, Coast Guard.

Target Market(s)

Federal government, all the armed forces , large government contractors in the security industry

Contact Information for Business Card

we want a QR code linking to our website

Logo Text

I want our name ORVA in the logo with the red white and blue color scheme srr pictures of our vehicles

Colors
ec1f27
ffffff
0255a3

Requirements
Must have
• name, position title, 2 or 3 phone numbers, e mail address
Nice to have
• some foil
Should not have
• n/a

```html
<!DOCTYPE html>
<html lang="en">
<head>
<meta charset="utf-8">
<title>ORVA Protective Services – Stationery</title>
<link href="https://fonts.googleapis.com/css2?family=Open+Sans:wght@400;600;700;800&display=swap" rel="stylesheet">
<style>
  :root {
    --brand-blue: #0255a3;
    --brand-red: #ec1f27;
    --paper: #ffffff;
    --ink: #555555;
    --ink-dark: #333333;
    --backdrop: #e4e5e7;
  }
  * { margin: 0; padding: 0; box-sizing: border-box; }
  html, body { width: 1200px; height: 1200px; overflow: hidden; }
  body {
    background: var(--backdrop);
    font-family: "Open Sans", Arial, sans-serif;
    position: relative;
  }
  .sheet {
    position: absolute;
    background: var(--paper);
    box-shadow: 0 2px 8px rgba(0,0,0,0.18);
    overflow: hidden;
  }
  .letterhead { left: 120px; top: 278px; width: 556px; height: 716px; }
  .envelope-front { left: 715px; top: 492px; width: 432px; height: 217px; }
  .envelope-back { left: 717px; top: 743px; width: 429px; height: 213px; }

  .brand {
    position: absolute;
    color: var(--brand-blue);
    font-weight: 800;
    line-height: 1;
  }
  .brand-name { display: block; letter-spacing: 2px; }
  .brand-tag { display: block; letter-spacing: 0.4px; }
  .letterhead .brand { left: 356px; top: 20px; }
  .letterhead .brand-name { font-size: 38px; }
  .letterhead .brand-tag { font-size: 10.6px; margin-top: 3px; }
  .envelope-front .brand { left: 20px; top: 22px; }
  .envelope-front .brand-name { font-size: 24px; letter-spacing: 1.4px; }
  .envelope-front .brand-tag { font-size: 7px; margin-top: 2px; }

  .letter-body {
    position: absolute;
    left: 52px; top: 131px; width: 450px;
    font-size: 8.6px; color: var(--ink); line-height: 11px;
  }
  .letter-body p { margin-bottom: 11px; }
  .letter-body .para { line-height: 16px; text-align: justify; margin-bottom: 16px; }
  .recipient { margin-top: 10px; margin-bottom: 30px !important; }
  .salutation { margin-bottom: 20px !important; }
  .closing { margin-top: 30px; margin-bottom: 8px !important; }
  .signature {
    width: 130px; height: 16px;
    background: linear-gradient(90deg, rgba(85,85,85,0.12), rgba(85,85,85,0.04));
    border-radius: 3px; margin-bottom: 12px;
  }
  .signer-name { font-size: 11.5px; color: var(--ink-dark); font-weight: 600; margin-bottom: 6px !important; }

  /* footer band: straight rules */
  .footer-band {
    position: absolute; left: 0; right: 0; bottom: 0;
    background: var(--brand-blue);
  }
  .footer-band::before, .footer-band::after {
    content: ""; position: absolute; left: 0; right: 0;
  }
  .footer-band::before { background: var(--brand-red); height: 5px; top: -13px; }
  .footer-band::after { background: var(--brand-blue); height: 3px; top: -5px; }
  .letterhead .footer-band { height: 92px; }
  .envelope-front .footer-band { height: 44px; }
  .envelope-front .footer-band::before { height: 4px; top: -11px; }
  .envelope-front .footer-band::after { height: 2px; top: -4px; }

  .footer-contact {
    position: absolute; left: 72px; bottom: 16px;
    color: #fff; font-family: Arial, Helvetica, sans-serif;
    font-size: 8.8px; line-height: 10.8px;
  }
  .footer-contact .address { margin-bottom: 7px; }
  .footer-contact .row { display: flex; align-items: center; gap: 4px; }
  .footer-contact svg { width: 8px; height: 8px; fill: #fff; }
  .return-address {
    position: absolute; left: 24px; bottom: 17px;
    color: #fff; font-size: 8.2px;
  }
  .flap { position: absolute; left: 0; top: 0; display: block; }
</style>
</head>
<body>

<section class="sheet letterhead">
  <div class="brand">
    <span class="brand-name">ORVA</span>
    <span class="brand-tag">PROTECTIVE SERVICES</span>
  </div>

  <div class="letter-body">
    <p>Issuing Date: May 5, 2018</p>
    <p class="recipient">Name Of Employee Mr. XYZABC<br>Address of Employee<br>Address Line 2 etc..</p>
    <p class="salutation">Dear Mr.XYZABC</p>
    <p class="para">Lorem Ipsum has been the industry's standard dummy text ever since the 1500s, when an unknown printer took a galley of type and scrambled it to make a type specimen book. It has survived not only five centuries, but also the leap into electronic typesetting, remaining essentially unchanged. It was popularised in the 1960s with the release of Letraset sheets containing Lorem Ipsum passages, and more recently with desktop publishing software like Aldus PageMaker including versions of Lorem Ipsum.</p>
    <p class="para">Lorem Ipsum is simply dummy text of the printing and typesetting industry. Lorem Ipsum has been the industry's standard dummy text ever since the 1500s, when an unknown printer took a galley of type and scrambled it to make a type specimen book.</p>
    <p class="para">It has survived not only five centuries, but also the leap into electronic typesetting, remaining essentially unchanged. It was popularised in the 1960s with the release of Letraset sheets containing Lorem Ipsum passages.</p>
    <p class="closing">Yours Sincerely</p>
    <div class="signature" role="img" aria-label="Handwritten signature of Daniel Mercer"></div>
    <p class="signer-name">Daniel Mercer</p>
    <p>Managing Director</p>
  </div>

  <div class="footer-band" aria-hidden="true"></div>
  <div class="footer-contact">
    <p class="address">2480 Harbor Point Dr<br>Ste. 310, Fairview, TX 75069</p>
    <p class="row"><svg viewBox="0 0 10 10"><path d="M1,3 Q5,0 9,3 L8,4.5 L6.5,3.8 L6.5,3 Q5,2.5 3.5,3 L3.5,3.8 L2,4.5Z M2.5,5 L7.5,5 L8.5,9 L1.5,9Z"/></svg>(855) 410-2276 | (469) 318-7704</p>
    <p class="row"><svg viewBox="0 0 10 10"><path d="M2.5,0.5 H7.5 V9.5 H2.5Z M3.5,1.5 V7.5 H6.5 V1.5Z"/></svg>(855) 410-2276</p>
    <p class="row"><svg viewBox="0 0 10 10"><path d="M0.5,2 H9.5 V8 H0.5Z M1,2.5 L5,5.5 L9,2.5" stroke="#0255a3" stroke-width="0.8"/></svg>info@orvaprotective.com</p>
    <p class="row"><svg viewBox="0 0 10 10"><circle cx="5" cy="5" r="4.5"/><path d="M5,0.5 V9.5 M0.5,5 H9.5" stroke="#0255a3" stroke-width="0.8"/></svg>www.orvaprotective.com</p>
  </div>
</section>

<section class="sheet envelope-front">
  <div class="brand">
    <span class="brand-name">ORVA</span>
    <span class="brand-tag">PROTECTIVE SERVICES</span>
  </div>
  <div class="footer-band" aria-hidden="true"></div>
  <p class="return-address">2480 Harbor Point Dr Ste. 310, Fairview, TX 75069</p>
</section>

<section class="sheet envelope-back">
  <svg class="flap" width="429" height="52" viewBox="0 0 429 52" aria-hidden="true">
    <path d="M0,0 H429 L414,51 H16Z" fill="var(--brand-blue)"/>
  </svg>
</section>

</body>
</html>
```